KRT Project Signage

Need a sign to be displayed in the front of properties currently under Construction or Renovation to advertise our company information. Need it to be Professional and Contemporary. We are a Design/Build Construction Company. Information should include Company Name, email, website, phone number. Attached: Logo and company brochure, also included and inspiration images

```html
<!DOCTYPE html>
<html lang="en">
<head>
<meta charset="utf-8">
<title>KRT Construction – Project Sign</title>
<link rel="stylesheet" href="https://fonts.googleapis.com/css2?family=Jost:wght@700&family=Poppins:wght@600;700;800&display=swap">
<style>
  :root {
    --backdrop: #a6a6a6;
    --sign-white: #ffffff;
    --ink: #0d0d0d;
    --yellow: #e8e23c;
    --yellow-light: #efe94e;
    --yellow-deep: #ddd631;
  }
  * { box-sizing: border-box; margin: 0; padding: 0; }
  html, body {
    width: 1200px; height: 3200px; overflow: hidden;
    background: var(--backdrop);
    font-family: "Poppins", sans-serif;
    color: var(--ink);
  }
  .sign {
    position: absolute; left: 100px; top: 850px;
    width: 1000px; height: 1500px;
    background: var(--sign-white);
    box-shadow: 10px 14px 24px rgba(0,0,0,.35);
    overflow: hidden;
  }
  .sign-shapes { position: absolute; inset: 0; width: 1000px; height: 1500px; }

  .brand {
    position: absolute; top: 150px; left: 0; width: 1000px;
    display: flex; justify-content: center; align-items: center; gap: 16px;
  }
  .brand-dot { width: 40px; height: 40px; border-radius: 50%; background: var(--yellow); }
  .brand-name {
    font-family: "Poppins", sans-serif; font-weight: 700;
    font-size: 38px; letter-spacing: 3px; color: var(--ink);
  }

  .person-name {
    position: absolute; top: 305px; left: 0; width: 1000px;
    text-align: center;
    font-family: "Jost", sans-serif; font-weight: 700;
    font-size: 148px; line-height: 132px; letter-spacing: -1px;
  }
  .role {
    position: absolute; top: 585px; left: 0; width: 1000px;
    text-align: center;
    font-family: "Poppins", sans-serif; font-weight: 800;
    font-size: 50px; letter-spacing: 11px; line-height: 60px;
  }

  .phone-pill {
    position: absolute; left: 95px; width: 785px; height: 92px;
    border-radius: 46px; overflow: hidden; display: flex;
    box-shadow: 0 6px 0 var(--sign-white), 0 10px 12px rgba(0,0,0,.28);
  }
  .phone-pill.direct { top: 888px; }
  .phone-pill.office { top: 1004px; }
  .phone-label {
    width: 256px; background: var(--sign-white);
    display: flex; align-items: center; padding-left: 30px;
    font-weight: 800; font-size: 49px; letter-spacing: .5px;
  }
  .phone-number {
    flex: 1; background: var(--ink); color: var(--sign-white);
    display: flex; align-items: center; gap: 14px; padding-left: 18px;
    font-weight: 700; font-size: 62px; letter-spacing: .5px;
  }
  .phone-icon { width: 58px; height: 58px; flex: none; }

  .contact-line {
    position: absolute; left: 100px; display: flex; align-items: flex-start; gap: 20px;
    font-weight: 600;
  }
  .contact-line.email { top: 1148px; font-size: 49px; line-height: 64px; align-items: center; }
  .contact-line.address { top: 1272px; font-size: 45px; line-height: 60px; }
  .contact-icon { width: 46px; height: 46px; flex: none; }
  .contact-line.address .contact-icon { margin-top: 10px; }
  .divider {
    position: absolute; left: 117px; top: 1243px; width: 770px; height: 2px;
    background: rgba(0,0,0,.35);
  }
</style>
</head>
<body>
  <main class="sign">
    <svg class="sign-shapes" viewBox="0 0 1000 1500" aria-hidden="true">
      <defs>
        <linearGradient id="panelFill" x1="0" y1="0" x2="0" y2="1">
          <stop offset="0" stop-color="var(--yellow-light)"/>
          <stop offset="1" stop-color="var(--yellow-deep)"/>
        </linearGradient>
      </defs>
      <polygon points="0,830 415,712 0,870" fill="var(--ink)"/>
      <polygon points="1000,830 585,712 1000,870" fill="var(--ink)"/>
      <polygon points="0,885 499,692 1000,885 1000,1500 0,1500" fill="url(#panelFill)"/>
    </svg>

    <div class="brand">
      <span class="brand-name">KRT CONSTRUCTION</span>
      <span class="brand-dot"></span>
    </div>

    <h1 class="person-name">MARION<br>ELLERY</h1>
    <p class="role">DESIGN AND BUILDER</p>

    <div class="phone-pill direct">
      <span class="phone-label">DIRECT</span>
      <span class="phone-number">
        <svg class="phone-icon" viewBox="0 0 58 58" aria-hidden="true">
          <circle cx="29" cy="29" r="28" fill="var(--yellow)"/>
          <path d="M20 15c2-1 4 0 5 2l2 5c1 2 0 3-1 4l-2 1c1 4 4 7 8 8l1-2c1-1 2-2 4-1l5 2c2 1 3 3 2 5l-1 3c-1 2-3 3-6 2-10-2-18-10-20-20-1-3 0-5 3-7z" fill="var(--ink)"/>
        </svg>555.201.4837
      </span>
    </div>
    <div class="phone-pill office">
      <span class="phone-label">OFFICE</span>
      <span class="phone-number">
        <svg class="phone-icon" viewBox="0 0 58 58" aria-hidden="true">
          <circle cx="29" cy="29" r="28" fill="var(--yellow)"/>
          <path d="M20 15c2-1 4 0 5 2l2 5c1 2 0 3-1 4l-2 1c1 4 4 7 8 8l1-2c1-1 2-2 4-1l5 2c2 1 3 3 2 5l-1 3c-1 2-3 3-6 2-10-2-18-10-20-20-1-3 0-5 3-7z" fill="var(--ink)"/>
        </svg>555.310.2264
      </span>
    </div>

    <p class="contact-line email">
      <svg class="contact-icon" viewBox="0 0 46 46" aria-hidden="true">
        <rect x="2" y="10" width="42" height="28" fill="var(--ink)"/>
        <polyline points="4,12 23,27 42,12" fill="none" stroke="var(--yellow)" stroke-width="3"/>
        <polyline points="4,36 18,23 M42,36 28,23" fill="none" stroke="var(--yellow)" stroke-width="3"/>
      </svg>
      jordan@krtconstruction.com
    </p>
    <div class="divider"></div>
    <p class="contact-line address">
      <svg class="contact-icon" viewBox="0 0 46 46" aria-hidden="true">
        <path d="M23 2c-9 0-15 7-15 15 0 11 15 24 15 24s15-13 15-24c0-8-6-15-15-15z" fill="var(--ink)"/>
        <circle cx="23" cy="17" r="6" fill="var(--yellow)"/>
        <ellipse cx="23" cy="42" rx="14" ry="3" fill="none" stroke="var(--ink)" stroke-width="3"/>
      </svg>
      <span>4815 Harbor Point Dr., Ste. 108<br>Lakeview, FL 33499</span>
    </p>
  </main>
</body>
</html>
```